Pawn & Gun store business card design

Hello! We would like a new business card design for our pawn & gun store. We loan money on items of value and sell firearms, jewelry, electronics & more.

Card will need to have the following information:

Business name - Prairie Nickel Pawn & Gun
Address - 2417 Hwy 53 S. Suite C Cedar Bluff, TX 75246
Employees name - Darren Kellum
Phone number - 972-613-8840
Email - PrairieNickelPawn@Mailvera.com
Website - PrairieNickelPawn.com

Somewhere on the card we would like it to say "Offering 10 Month Layaway!" & "We buy & loan on anything of value!". Our main store color is orange (please see logo). Logo does not have to be on the business card but it can be. Would like the back to have an area to write a note on the back. We like vintage things like old coins, collectables, firearms and more so think about this in the design. We want a business card as unique as our store!

Colors

Designer to choose colors to be used in the design.

Requirements
Nice to have
• Vintage Style

```html
<!DOCTYPE html>
<html lang="en">
<head>
<meta charset="utf-8">
<title>Prairie Nickel Pawn &amp; Gun — Business Card</title>
<link href="https://fonts.googleapis.com/css2?family=Oswald:wght@300;400;600;700&display=swap" rel="stylesheet">
<style>
  :root {
    --backdrop: #9b9b9b;
    --paper: #f7f6f3;
    --ink: #4a2e1f;
    --orange: #e2682f;
    --edge: #e07a1c;
  }
  * { box-sizing: border-box; margin: 0; padding: 0; }
  html, body { width: 1200px; height: 1059px; overflow: hidden; }
  body {
    background: var(--backdrop);
    font-family: "Oswald", "Arial Narrow", sans-serif;
    color: var(--ink);
    position: relative;
  }
  .card {
    position: absolute;
    background: var(--paper);
    border-bottom: 4px solid var(--edge);
    box-shadow: 0 18px 36px rgba(0,0,0,.28);
  }

  /* Front */
  .card-front { left: 60px; top: 190px; width: 380px; height: 665px; padding: 20px; }
  .front-frame {
    height: 100%;
    border: 3px solid var(--ink);
    display: flex; flex-direction: column;
  }
  .icon-row { display: flex; height: 140px; border-bottom: 3px solid var(--ink); }
  .icon-cell { flex: 1; display: flex; align-items: center; justify-content: center; }
  .icon-cell + .icon-cell { border-left: 3px solid var(--ink); }
  .icon-art { width: 90px; height: 70px; border-radius: 6px; }
  .icon-art.revolver { background: linear-gradient(135deg, #6b4a38, var(--ink)); }
  .icon-art.gem { background: linear-gradient(135deg, #8a6a58, var(--ink)); width: 70px; }

  .name-band {
    background: var(--orange);
    height: 108px;
    display: flex; align-items: center; justify-content: center;
    border-bottom: 3px solid var(--ink);
    padding: 0 14px;
  }
  .employee-name { font-weight: 600; font-size: 42px; letter-spacing: 1px; text-transform: uppercase; color: var(--ink); white-space: nowrap; }

  .info-row {
    flex: 1;
    display: flex; flex-direction: column; justify-content: center;
    padding: 0 18px;
    text-transform: uppercase;
    line-height: 1.15;
    white-space: nowrap;
  }
  .info-row + .info-row { border-top: 3px solid var(--ink); }
  .business-name { font-weight: 600; font-size: 24px; }
  .address { font-weight: 300; font-size: 14px; letter-spacing: .2px; }
  .phone { font-weight: 400; font-size: 52px; line-height: 1; }
  .email { font-weight: 300; font-size: 16px; }
  .website { font-weight: 600; font-size: 22px; }
  .offer { font-weight: 700; font-size: 23px; }
  .offer-sub { font-weight: 300; font-size: 16px; }

  /* Back */
  .card-back { left: 480px; top: 340px; width: 665px; height: 380px; padding: 22px; }
  .back-frame {
    height: 100%;
    border: 3px solid var(--ink);
    display: flex; flex-direction: column; align-items: center; justify-content: center;
  }
  .brand { display: flex; align-items: center; gap: 12px; }
  .brand-mark { width: 22px; height: 22px; border-radius: 50%; background: var(--orange); }
  .brand-name { font-weight: 600; font-size: 34px; color: var(--orange); text-transform: uppercase; letter-spacing: 1px; }
  .brand-place { margin-top: 6px; font-weight: 400; font-size: 13px; letter-spacing: 2px; text-transform: uppercase; }
  .note-space { height: 140px; }
</style>
</head>
<body>

<article class="card card-front">
  <div class="front-frame">
    <div class="icon-row">
      <div class="icon-cell"><div class="icon-art revolver" role="img" aria-label="Engraved vintage revolver illustration"></div></div>
      <div class="icon-cell"><div class="icon-art gem" role="img" aria-label="Engraved diamond illustration"></div></div>
    </div>
    <div class="name-band"><h1 class="employee-name">Darren Kellum</h1></div>
    <div class="info-row">
      <p class="business-name">Prairie Nickel Pawn &amp; Gun</p>
      <p class="address">2417 Hwy 53 S. Suite C Cedar Bluff, TX 75246</p>
    </div>
    <div class="info-row">
      <p class="phone">972-613-8840</p>
      <p class="email">PrairieNickelPawn@Mailvera.com</p>
    </div>
    <div class="info-row">
      <p class="website">www.PrairieNickelPawn.com</p>
    </div>
    <div class="info-row">
      <p class="offer">Offering 10 Month Layaway</p>
      <p class="offer-sub">We buy &amp; loan on anything of value</p>
    </div>
  </div>
</article>

<article class="card card-back">
  <div class="back-frame">
    <div class="brand">
      <span class="brand-mark"></span>
      <span class="brand-name">Prairie Nickel Pawn</span>
    </div>
    <p class="brand-place">Cedar Bluff, TX</p>
    <div class="note-space"></div>
  </div>
</article>

</body>
</html>
```